furniture and home contents restoration

I need to list the services that we perform in our studio.
we serve the general public as well as the insurance/ remediation industry

```html
<!DOCTYPE html>
<html lang="en">
<head>
<meta charset="utf-8">
<title>Keystone Refinishers – Business Card</title>
<link rel="stylesheet" href="https://fonts.googleapis.com/css2?family=Noto+Serif:wght@400;700&display=swap">
<style>
  :root {
    --backdrop: #2a2a2c;
    --card-dark: #1f2f38;
    --card-light: #ffffff;
    --ink-dark: #1c2b33;
    --ink-light: #ffffff;
  }
  * { margin: 0; padding: 0; box-sizing: border-box; }
  html, body {
    width: 1200px; height: 900px; overflow: hidden;
    background: var(--backdrop);
    font-family: "Noto Serif", Georgia, serif;
  }
  .canvas { position: relative; width: 1200px; height: 900px; }
  .card {
    position: absolute; left: 250px; width: 700px; height: 400px;
    border-radius: 18px;
  }
  .card-back {
    top: 40px; background: var(--card-dark); color: var(--ink-light);
    padding: 28px 36px 0;
  }
  .card-front {
    top: 460px; background: var(--card-light); color: var(--ink-dark);
    text-align: center;
  }
  .services-title {
    text-align: center; font-size: 22px; font-weight: 700; letter-spacing: 0.5px;
    margin-bottom: 18px;
  }
  .service-columns { display: flex; justify-content: space-between; }
  .service-list { list-style: none; font-size: 11.5px; line-height: 15.5px; text-transform: uppercase; }
  .service-list li::before { content: "• "; }
  .service-list.right { margin-top: 20px; }
  .service-extras {
    text-align: center; font-size: 15.5px; line-height: 20px; margin-top: 8px;
    text-transform: uppercase;
  }
  .company-name {
    font-size: 46px; font-weight: 700; letter-spacing: 1px; padding-top: 58px;
  }
  .person-name { font-size: 24px; font-weight: 700; margin-top: 30px; }
  .contact { font-size: 16px; line-height: 24px; margin-top: 6px; text-transform: uppercase; }
  .contact b { font-weight: 700; }
  .tagline {
    position: absolute; left: 34px; bottom: 42px;
    font-size: 14.5px; text-transform: uppercase; letter-spacing: 0.3px;
  }
</style>
</head>
<body>
<main class="canvas">
  <section class="card card-back">
    <h2 class="services-title">HOME CONTENTS RESTORATION</h2>
    <div class="service-columns">
      <ul class="service-list left">
        <li>Antique repair and restoration</li>
        <li>Art cleaning and remounting</li>
        <li>Art and mirror frame repair</li>
        <li>Chandelier cleaning and restoration</li>
        <li>Document restoration</li>
        <li>Glass, ceramic, and mirror repair</li>
        <li>Hardware repair and restoration</li>
        <li>Kitchen removal and reinstallation</li>
        <li>Lamp cleaning and restoration</li>
        <li>Lamp shade replacement</li>
      </ul>
      <ul class="service-list right">
        <li>Metal polishing and restoration</li>
        <li>Odor removal and ozone services</li>
        <li>Photo restoration</li>
        <li>Upholstery cleaning and deodorizing</li>
        <li>In-house upholstery and reupholstery</li>
        <li>Rug cleaning and restoration</li>
        <li>Musical instrument restoration</li>
        <li>Window treatment repair/ restoration</li>
        <li>Leather restoration and replacement</li>
        <li>Piano restoration and repair</li>
      </ul>
    </div>
    <p class="service-extras">On-site inspections and desk review services<br>Assessment reports and estimates for repair and restoration</p>
  </section>

  <section class="card card-front">
    <h1 class="company-name">KEYSTONE REFINISHERS</h1>
    <p class="person-name">DANIEL MORETTI</p>
    <p class="contact">
      <b>O</b> -555.210.4800 <b>M</b> -555.318.2290 <b>F</b> -555.210.4815<br>
      12 Mill Brook Rd. Riverton, NY 10000<br>
      info@keystonerefinish.com
    </p>
    <p class="tagline">Serving the general public and the insurance industry for over 40 years</p>
  </section>
</main>
</body>
</html>
```